Vantrel System Web Page Design

This project is to design 6 pages of a web based medical system for clinics, hospitals, drugs suppliers, general items suppliers, insurance company, laboratories and patients (basically all parties which could be involved in).We want the designs of the browser, button, icon and layout are based on Zeltor, which is user friendly, looks professional, simple and neat but with powerful functions. We have uploaded few pictures of another system, please do not copy its design because this is not what we are looking for, the pictures are for you to know the elements should be included in our pages. Vantrel web-base system, design 6 pages1. Login PageShould include the following elements-company id with input field-login id with input field-password with input field2. Main Page (Navigation page)Should include the following elements-Appointment-Consultation-Patient-Drugs inventory -General supplies inventory -Laboratory-Suppliers-Insurance-Reports 3. Appointment PageShould include all the the elements in the respective pictures plus the followings-Daily View, Weekly View, Monthly View buttons4. Consultation PageShould include all the the elements in the respective picture5. Patient Page5.1 General information Should include all the the elements in the respective picture5.2 medical history/lab reportsShould include all the the elements in the respective picture plus the followings-Notify patient button-Share report button.
Updated on 28 Nov:
Please stop using Harbor Suite in your designs which is not the name of our system. We have just rename our system to Vantrel, please take note.
We need the system to look professional not playful, do not use too many colors and playful icons.

```html
<!DOCTYPE html>
<html lang="en">
<head>
<meta charset="utf-8">
<title>Vantrel – Reports</title>
<link href="https://fonts.googleapis.com/css2?family=Roboto:wght@400;500;700&display=swap" rel="stylesheet">
<style>
  :root {
    --brand: #1d5ca8;
    --brand-dark: #17508f;
    --ink: #222428;
    --muted: #686b72;
    --line: #d9dade;
    --side-bg: #ebecef;
    --page-bg: #fafafa;
    --white: #ffffff;
  }
  * { box-sizing: border-box; margin: 0; padding: 0; }
  html, body { width: 1200px; height: 674px; overflow: hidden; }
  body { font-family: "Roboto", Arial, sans-serif; background: var(--page-bg); color: var(--ink); position: relative; }

  .topbar { position: absolute; left: 0; top: 0; width: 1200px; height: 81px; background: var(--white); border-bottom: 1px solid #c9cacd; }
  .brand { position: absolute; left: 24px; top: 22px; display: flex; align-items: center; gap: 12px; }
  .brand-mark { width: 26px; height: 26px; background: var(--brand); border-radius: 3px; }
  .brand-name { font-size: 27px; font-weight: 500; color: var(--brand); letter-spacing: 0.2px; }
  .user { position: absolute; left: 956px; top: 12px; display: flex; align-items: center; }
  .user-avatar { width: 58px; height: 58px; border-radius: 50%; background: radial-gradient(circle at 50% 40%, #c9b8a6, #7d8794 70%); border: 1px solid #d4d4d4; }
  .user-name { margin-left: 13px; font-size: 17px; color: var(--ink); }
  .user-toggle { position: absolute; left: 188px; top: 21px; }

  .sidebar { position: absolute; left: 0; top: 82px; width: 202px; height: 592px; background: var(--side-bg); border-right: 1px solid #d0d1d4; }
  .nav { position: absolute; top: 17px; left: 0; width: 202px; list-style: none; }
  .nav-item { position: relative; display: flex; align-items: center; justify-content: space-between; padding: 0 14px 0 13px; font-size: 17px; font-weight: 700; color: var(--muted); border-bottom: 1px solid #d6d7db; height: 31px; line-height: 19px; }
  .nav-item.first { height: 44px; padding-top: 0; }
  .nav-item.tall { height: 49px; }
  .nav-item.active { background: var(--brand); color: var(--white); border-bottom: none; height: 31px; }
  .nav-item svg { flex: none; }

  .filters { position: absolute; left: 250px; top: 113px; width: 896px; display: flex; justify-content: space-between; }
  .select { width: 426px; height: 38px; background: var(--white); border: 1px solid var(--line); border-radius: 3px; display: flex; align-items: center; justify-content: space-between; padding: 0 10px 0 9px; font-size: 15px; color: var(--ink); }

  .report-table { position: absolute; left: 251px; top: 176px; width: 895px; height: 369px; background: var(--white); border: 1px solid var(--line); border-radius: 3px; overflow: hidden; }
  .report-row { position: relative; height: 31.2px; border-bottom: 1px solid #e2e3e6; font-size: 13px; }
  .report-row:first-child { height: 28px; }
  .report-row span { position: absolute; top: 50%; transform: translateY(-50%); }
  .report-name { left: 15px; color: #3a3c40; }
  .report-action { color: #3a3c40; text-decoration: underline; transform: translate(-50%, -50%) !important; }
  .act-export { left: 555px; }
  .act-delete { left: 655px; }
  .act-rename { left: 763px; }
  .act-view { left: 850px; }
  .scroll-thumb { position: absolute; left: 886px; top: 208px; width: 7px; height: 88px; background: #8d8f94; border-radius: 4px; }

  .actions { position: absolute; left: 252px; top: 586px; display: flex; gap: 15px; }
  .btn { height: 37px; border: 2px solid var(--brand); border-radius: 4px; background: var(--white); color: var(--brand); font-size: 16px; display: flex; align-items: center; justify-content: center; font-family: inherit; }
  .btn-scan { width: 104px; }
  .btn-video, .btn-import, .btn-return { width: 111px; margin-left: 1px; }
</style>
</head>
<body>
  <header class="topbar">
    <div class="brand">
      <span class="brand-mark"></span>
      <span class="brand-name">Vantrel</span>
    </div>
    <div class="user">
      <div class="user-avatar" role="img" aria-label="Profile photo of the signed-in user"></div>
      <span class="user-name">Daniel Reyes</span>
      <svg class="user-toggle" width="18" height="12" viewBox="0 0 18 12"><path d="M2 2 L9 9 L16 2" fill="none" stroke="var(--brand)" stroke-width="3"/></svg>
    </div>
  </header>

  <aside class="sidebar">
    <ul class="nav">
      <li class="nav-item first">Appointments
        <svg width="18" height="16" viewBox="0 0 18 16"><rect x="1" y="2" width="16" height="13" fill="none" stroke="var(--brand)" stroke-width="1.4"/><path d="M1 5.5h16M5 8h1M8.5 8h1M12 8h1M5 11h1M8.5 11h1M12 11h1" stroke="var(--brand)" stroke-width="1.4"/></svg></li>
      <li class="nav-item">Consultation
        <svg width="18" height="16" viewBox="0 0 18 16"><path d="M3 14 C3 8 8 3 15 2 M5 14 C6 10 10 6 15 5 M3 14h12" fill="none" stroke="#7a8aa0" stroke-width="1.4"/></svg></li>
      <li class="nav-item">Patient
        <svg width="18" height="16" viewBox="0 0 18 16"><circle cx="7" cy="5" r="2.5" fill="none" stroke="#7a8aa0" stroke-width="1.4"/><path d="M1 9h16v4H1zM2 13v2M16 13v2" fill="none" stroke="#7a8aa0" stroke-width="1.4"/></svg></li>
      <li class="nav-item">Drugs inventory
        <svg width="18" height="16" viewBox="0 0 18 16"><rect x="2" y="5" width="14" height="10" rx="1" fill="none" stroke="#7a8aa0" stroke-width="1.4"/><path d="M6 5V2h6v3M9 7.5v5M6.5 10h5" fill="none" stroke="#7a8aa0" stroke-width="1.4"/></svg></li>
      <li class="nav-item tall">General supplies<br>inventory
        <svg width="18" height="16" viewBox="0 0 18 16"><rect x="1" y="1" width="16" height="14" rx="1.5" fill="none" stroke="var(--brand)" stroke-width="1.4"/><path d="M4 5h10M4 8h10M6 11h6" stroke="var(--brand)" stroke-width="1.4"/></svg></li>
      <li class="nav-item">Laboratory
        <svg width="18" height="16" viewBox="0 0 18 16"><path d="M3 2v11a2 2 0 0 0 4 0V2M11 2v11a2 2 0 0 0 4 0V2M1 14h16" fill="none" stroke="#7a8aa0" stroke-width="1.4"/></svg></li>
      <li class="nav-item">Suppliers
        <svg width="18" height="16" viewBox="0 0 18 16"><circle cx="3.5" cy="3" r="1.6" fill="none" stroke="#7a8aa0" stroke-width="1.2"/><circle cx="9" cy="3" r="1.6" fill="none" stroke="#7a8aa0" stroke-width="1.2"/><circle cx="14.5" cy="3" r="1.6" fill="none" stroke="#7a8aa0" stroke-width="1.2"/><circle cx="9" cy="11" r="3.5" fill="none" stroke="#7a8aa0" stroke-width="1.4"/></svg></li>
      <li class="nav-item">Insurance
        <svg width="18" height="16" viewBox="0 0 18 16"><path d="M9 1 L15 3 V8 C15 11.5 12 14 9 15 C6 14 3 11.5 3 8 V3 Z" fill="none" stroke="var(--brand)" stroke-width="1.4"/><path d="M7 6h4M9 6v4" stroke="var(--brand)" stroke-width="1.4"/></svg></li>
      <li class="nav-item active">Reports
        <svg width="18" height="16" viewBox="0 0 18 16"><rect x="4" y="1" width="11" height="14" rx="1" fill="none" stroke="#ffffff" stroke-width="1.4"/><path d="M7 5h5M7 8h5M7 11h5" stroke="#ffffff" stroke-width="1.4"/></svg></li>
    </ul>
  </aside>

  <main>
    <div class="filters">
      <div class="select">Select Report Type
        <svg width="17" height="11" viewBox="0 0 17 11"><path d="M2 2 L8.5 8.5 L15 2" fill="none" stroke="var(--brand)" stroke-width="3"/></svg></div>
      <div class="select">Select Date
        <svg width="17" height="11" viewBox="0 0 17 11"><path d="M2 2 L8.5 8.5 L15 2" fill="none" stroke="var(--brand)" stroke-width="3"/></svg></div>
    </div>

    <section class="report-table">
      <div class="report-row"><span class="report-name">Pulmonary CT</span><span class="report-action act-export">Export</span><span class="report-action act-delete">Delete</span><span class="report-action act-rename">Rename</span><span class="report-action act-view">View</span></div>
      <div class="report-row"><span class="report-name">Pulmonary CT</span><span class="report-action act-export">Export</span><span class="report-action act-delete">Delete</span><span class="report-action act-rename">Rename</span><span class="report-action act-view">View</span></div>
      <div class="report-row"><span class="report-name">Pulmonary CT</span><span class="report-action act-export">Export</span><span class="report-action act-delete">Delete</span><span class="report-action act-rename">Rename</span><span class="report-action act-view">View</span></div>
      <div class="report-row"><span class="report-name">Pulmonary CT</span><span class="report-action act-export">Export</span><span class="report-action act-delete">Delete</span><span class="report-action act-rename">Rename</span><span class="report-action act-view">View</span></div>
      <div class="report-row"><span class="report-name">Pulmonary CT</span><span class="report-action act-export">Export</span><span class="report-action act-delete">Delete</span><span class="report-action act-rename">Rename</span><span class="report-action act-view">View</span></div>
      <div class="report-row"><span class="report-name">Pulmonary CT</span><span class="report-action act-export">Export</span><span class="report-action act-delete">Delete</span><span class="report-action act-rename">Rename</span><span class="report-action act-view">View</span></div>
      <div class="report-row"><span class="report-name">Pulmonary CT</span><span class="report-action act-export">Export</span><span class="report-action act-delete">Delete</span><span class="report-action act-rename">Rename</span><span class="report-action act-view">View</span></div>
      <div class="report-row"><span class="report-name">Pulmonary CT</span><span class="report-action act-export">Export</span><span class="report-action act-delete">Delete</span><span class="report-action act-rename">Rename</span><span class="report-action act-view">View</span></div>
      <div class="report-row"><span class="report-name">Pulmonary CT</span><span class="report-action act-export">Export</span><span class="report-action act-delete">Delete</span><span class="report-action act-rename">Rename</span><span class="report-action act-view">View</span></div>
      <div class="report-row"><span class="report-name">Pulmonary CT</span><span class="report-action act-export">Export</span><span class="report-action act-delete">Delete</span><span class="report-action act-rename">Rename</span><span class="report-action act-view">View</span></div>
      <div class="report-row"></div>
      <div class="scroll-thumb"></div>
    </section>

    <div class="actions">
      <button class="btn btn-scan">Scan</button>
      <button class="btn btn-video">Video</button>
      <button class="btn btn-import">Import</button>
      <button class="btn btn-return">Return</button>
    </div>
  </main>
</body>
</html>
```